LoopVane - A ride hailing server VAR

our Brindle.co profile: https://brindle.co/517loopvane

LOOPVANE offers first world solutions to first world problems. These days, our smartphones are our cameras, our wallets and our ride home. LOOPVANE guarantees that even if your phone is lost or dies, you'll never get stranded again. Simply call or text (SMS) our toll-free number to request a ride, and choose from one of the various services you subscribe to. LOOPVANE verifies your identity through a unique pin, making it possible to request rides through your own account from a stranger's phone via text or phone call. You can also login through our website or our App, making it easier than ever to get home phoneless.

LOOPVANE is a heterogeneous ride-hailing service that allows users for request transportation from any "transportation network company," taxi, helicopter service, jet service or any transportation service company that is publicly available. LOOPVANE will allow users to connect through our site, automated phone system, App or any appropriated touch point available.

Target Market(s)

RIde Haling

Coding

Coded - Design and coding required

Number of Pages Required

4 page

Requirements
Must have
• hav
Nice to have
• e the same functionality as our competitor's site: https://hopquill.com/
Should not have
• should not be cheezy
• We need to have the registration/sign up on the main page like https://www.zarvix.com/

```html
<!DOCTYPE html>
<html lang="en">
<head>
<meta charset="utf-8">
<title>LOOPVANE</title>
<link href="https://fonts.googleapis.com/css2?family=Lato:wght@300;400;700;900&family=Cabin:wght@600;700&display=swap" rel="stylesheet">
<style>
:root{
  --ink:#1e1509;
  --gold:#f7c31a;
  --amber:#f5a82a;
  --btn:#e6a832;
  --hero-bg:#efefef;
  --road:#a2b8d0;
  --about-bg:#e8e8e8;
  --footer:#222222;
  --text:#555555;
  --white:#ffffff;
}
*{margin:0;padding:0;box-sizing:border-box}
html,body{width:994px;height:1200px;overflow:hidden;background:var(--white);font-family:"Lato",sans-serif}
.page{position:relative;width:994px;height:1200px}

.top-bar{position:absolute;top:0;left:0;width:994px;height:76px;background:var(--white)}
.brand{position:absolute;left:72px;top:8px;display:flex;align-items:center;gap:10px}
.brand-square{width:57px;height:57px;border-radius:6px;background:var(--amber)}
.brand-name{font-family:"Lato",sans-serif;font-weight:900;font-size:37px;letter-spacing:3px;color:var(--ink)}
.partners{position:absolute;right:71px;top:17px;display:flex;gap:13px}
.partner{width:105px;height:38px;border-radius:14px 20px 10px 10px;background:var(--amber);color:var(--white);font-weight:700;font-size:11px;letter-spacing:1px;display:flex;align-items:center;justify-content:center}

.main-nav{position:absolute;top:76px;left:0;width:994px;height:53px;background:var(--ink)}
.nav-links{position:absolute;left:71px;top:0;display:flex;height:53px}
.nav-links a{display:flex;align-items:center;padding:0 12px;color:#c9c4bb;text-decoration:none;font-size:12px;font-weight:700;letter-spacing:1.5px;height:53px;position:relative}
.nav-links a.active{color:var(--white)}
.nav-links a.active::after{content:"";position:absolute;left:0;right:0;bottom:0;height:2px;background:var(--amber)}
.nav-social{position:absolute;right:74px;top:19px;display:flex;gap:14px}
.nav-social span{width:14px;height:14px;border-radius:50%;background:#c9c4bb}

.hero{position:absolute;top:129px;left:0;width:994px;height:333px;background:var(--hero-bg);overflow:hidden}
.hero-road{position:absolute;left:0;bottom:0;width:994px;height:59px;background:var(--road)}
.hero-art{position:absolute;left:470px;top:10px;width:440px;height:318px;border-radius:6px;background:linear-gradient(180deg,#e3e3e3 0%,#dcdcdc 55%,#f4b431 56%,#f4b431 80%,#3a3a3a 81%,#3a3a3a 100%);opacity:.95}
.hero-copy{position:absolute;left:66px;top:104px}
.hero-kicker{font-weight:900;font-size:28px;letter-spacing:3px;color:var(--gold);padding-left:6px;line-height:1}
.hero-title{font-weight:900;font-size:46px;letter-spacing:4px;color:var(--gold);line-height:1.05}
.btn-signup{display:inline-block;margin-top:12px;width:106px;height:38px;background:#222;color:var(--white);font-weight:900;font-size:12px;letter-spacing:1.5px;text-align:center;line-height:38px;border-radius:2px}

.services{position:absolute;top:462px;left:0;width:994px;height:271px;background:var(--white)}
.section-title{position:absolute;top:48px;left:0;width:994px;text-align:center;font-weight:700;font-size:24px;letter-spacing:4px;color:#222}
.service{position:absolute;top:128px;display:flex;gap:10px}
.service-icon{width:79px;height:79px;border-radius:50%;background:var(--amber);flex:none;display:flex;align-items:center;justify-content:center}
.service h3{font-family:"Cabin",sans-serif;font-weight:700;font-size:21px;line-height:28px;color:var(--amber);margin-top:-2px}
.service p{font-size:10.5px;color:#222;line-height:19px;margin-top:2px}

.about{position:absolute;top:733px;left:0;width:994px;height:349px;background:var(--about-bg)}
.about h2{position:absolute;left:72px;top:48px;font-weight:400;font-size:28px;letter-spacing:3px;color:#222}
.about p{position:absolute;left:72px;top:100px;width:428px;font-size:11.4px;line-height:21.8px;color:var(--text);text-align:justify}
.btn-more{position:absolute;left:72px;top:237px;width:104px;height:42px;background:var(--btn);color:#222;font-size:13px;line-height:42px;text-align:center;border-radius:2px}
.video{position:absolute;left:533px;top:49px;width:390px;height:234px;background:#000}
.video-frame{position:absolute;left:0;top:21px;width:390px;height:186px;background:linear-gradient(180deg,#8d9a7e 0%,#6f8456 60%,#7b9a4e 100%)}
.video-play{position:absolute;left:165px;top:95px;width:60px;height:42px;border-radius:10px;background:rgba(30,30,30,.85)}
.video-controls{position:absolute;left:0;bottom:0;width:390px;height:27px;background:#1b1b1b;border-top:3px solid #444}

.footer{position:absolute;top:1082px;left:0;width:994px;height:118px;background:var(--footer)}
.footer-social{position:absolute;top:34px;left:0;width:994px;display:flex;justify-content:center;gap:10px}
.footer-social span{width:17px;height:17px;border-radius:50%;background:var(--white)}
.copyright{position:absolute;top:71px;left:0;width:994px;text-align:center;font-size:10.5px;color:var(--white)}
</style>
</head>
<body>
<div class="page">
  <header class="top-bar">
    <div class="brand"><span class="brand-square"></span><span class="brand-name">LOOPVANE</span></div>
    <div class="partners">
      <span class="partner">ZARVIX</span>
      <span class="partner">PELLORA</span>
      <span class="partner">TAXI</span>
    </div>
  </header>

  <nav class="main-nav">
    <div class="nav-links">
      <a class="active" href="#">HOME</a>
      <a href="#">ABOUT</a>
      <a href="#">WHAT WE DO</a>
      <a href="#">SUPPORT</a>
      <a href="#">CONTACT</a>
      <a href="#">SIGN IN</a>
    </div>
    <div class="nav-social"><span></span><span></span><span></span><span></span></div>
  </nav>

  <section class="hero">
    <div class="hero-road"></div>
    <div class="hero-art" role="img" aria-label="Illustration of a yellow taxi in front of a grey city skyline"></div>
    <div class="hero-copy">
      <div class="hero-kicker">WELCOME TO</div>
      <div class="hero-title">LOOPVANE</div>
      <a class="btn-signup">SIGN UP</a>
    </div>
  </section>

  <section class="services">
    <h2 class="section-title">WHAT WE DO</h2>
    <div class="service" style="left:72px">
      <div class="service-icon">
        <svg width="26" height="26" viewBox="0 0 24 24"><path fill="#222" d="M6.6 10.8c1.4 2.8 3.8 5.1 6.6 6.6l2.2-2.2c.3-.3.7-.4 1-.2 1.1.4 2.3.6 3.6.6.6 0 1 .4 1 1V20c0 .6-.4 1-1 1C10.6 21 3 13.4 3 4c0-.6.4-1 1-1h3.5c.6 0 1 .4 1 1 0 1.3.2 2.5.6 3.6.1.3 0 .7-.2 1l-2.3 2.2z"/></svg>
      </div>
      <div><h3>555 010 246<br>CALL OR TEXT (SMS)</h3><p>Our toll-free number to request a ride,</p></div>
    </div>
    <div class="service" style="left:362px">
      <div class="service-icon">
        <svg width="22" height="30" viewBox="0 0 16 24"><path fill="#222" d="M10 0L2 13h5l-3 11 9-14H8z"/></svg>
      </div>
      <div><h3>CHOOSE YOUR<br>SERVICES</h3><p>Choose from one of the various services</p></div>
    </div>
    <div class="service" style="left:651px">
      <div class="service-icon">
        <svg width="32" height="28" viewBox="0 0 32 28"><ellipse cx="16" cy="12" rx="15" ry="11" fill="#222"/><path d="M6 19l-3 8 9-5z" fill="#222"/><circle cx="10" cy="12" r="2" fill="#f5a82a"/><circle cx="16" cy="12" r="2" fill="#f5a82a"/><circle cx="22" cy="12" r="2" fill="#f5a82a"/></svg>
      </div>
      <div><h3>IDENTITY&nbsp; PIN</h3><p>Verifies your identity through<br>a unique pin</p></div>
    </div>
  </section>

  <section class="about">
    <h2>ABOUT LOOPVANE</h2>
    <p>LOOPVANE offers first world solutions to first world problems. These days, our smartphones are our cameras, our wallets and our ride home. LOOPVANE guarantees that even if your phone is lost or dies, you'll never get stranded again. Simply call or text (SMS) our toll-free number to request a ride, and choose from one of the various services you subscribe to. LOOPVANE verifies your identity</p>
    <a class="btn-more">READ MORE</a>
    <div class="video">
      <div class="video-frame" role="img" aria-label="Video still of a presenter holding a phone in a park"></div>
      <div class="video-play"><svg width="60" height="42" viewBox="0 0 60 42"><path d="M25 13l12 8-12 8z" fill="#fff"/></svg></div>
      <div class="video-controls"><svg width="390" height="24" viewBox="0 0 390 24"><path d="M16 7l9 5-9 5z" fill="#aaa"/><rect x="46" y="9" width="4" height="6" fill="#aaa"/><path d="M50 9l5-4v14l-5-4z" fill="#aaa"/></svg></div>
    </div>
  </section>

  <footer class="footer">
    <div class="footer-social"><span></span><span></span><span></span><span></span><span></span></div>
    <div class="copyright">© copyright 2017 LOOPVANE. All rights reserved.</div>
  </footer>
</div>
</body>
</html>
```